PRISM Marketing Campaign Schools 2025

We are seeking a professional, eye-catching, double-sided A4 flyer to promote our PRISM LED video walls to primary and secondary schools across Victoria. The flyer should communicate the benefits of our product in a clear and engaging way, targeting school decision-makers, and encourage immediate action. Full design brief is in the attachments.

Target Market(s)

School decision makers and buyers, school Principals and school business managers

Industry/Entity Type

Audio Visual products to schools for teaching and student engagement

Colors
EB3D1F
EC4F4E
F09395
F8D3D4
FCEDEE

Requirements
Must have
• Content to Include: • PRISM LED video wall logo • Show that we are located in Melbourne, Sydney, Brisbane, Perth • Website: www.vantoraglow.com.au • Strong call-to-action: Free on-site demonstration at your school
Nice to have
• Design Style: • Bright, modern, and professional. • Appealing to school administrators and teachers. • Visually highlight the product (images of the PRISM LED video wall in use). • Double-sided, full colour.

```html
<!DOCTYPE html>
<html lang="en">
<head>
<meta charset="utf-8">
<title>PRISM LED Video Walls for Schools</title>
<link rel="stylesheet" href="https://fonts.googleapis.com/css2?family=Montserrat:wght@700;800;900&family=Open+Sans:wght@400;600;700&display=swap">
<style>
  :root {
    --red: #eb3d1f;
    --red-soft: #ec4f4e;
    --pink: #f09395;
    --blush: #f8d3d4;
    --mist: #fcedee;
    --ink: #1d1d1d;
    --black: #111111;
    --white: #ffffff;
  }
  * { margin: 0; padding: 0; box-sizing: border-box; }
  html, body { width: 849px; height: 1200px; overflow: hidden; background: var(--white); }
  .flyer {
    position: relative; width: 849px; height: 1200px; overflow: hidden;
    font-family: "Open Sans", Arial, sans-serif; color: var(--ink);
  }
  .hero {
    position: absolute; top: 0; left: 0; width: 849px; height: 395px;
    background: var(--red); color: var(--white); padding: 30px 34px 0;
  }
  .hero h1 {
    font-family: "Montserrat", Arial, sans-serif; font-weight: 900;
    font-size: 31px; letter-spacing: 0.3px; margin-bottom: 12px;
  }
  .hero p { font-size: 14.4px; line-height: 1.42; max-width: 770px; margin-bottom: 14px; }
  .gallery {
    position: absolute; top: 268px; left: 34px; right: 34px;
    display: flex; gap: 20px;
  }
  .gallery .shot {
    flex: 1; height: 242px; border: 6px solid var(--white);
    box-shadow: 0 3px 10px rgba(0,0,0,.25);
  }
  .shot-hall { background: linear-gradient(160deg, #3d2a22, #7c4a2f 55%, #2a1d18); }
  .shot-outdoor { background: linear-gradient(170deg, #6f8aa0, #3a4b5a 45%, #4f6b3a); }
  .shot-sports { background: linear-gradient(165deg, #2b2b33, #8a3a3a 50%, #1f1f24); }
  .content { position: absolute; top: 540px; left: 34px; right: 34px; }
  .content h2 {
    font-family: "Montserrat", Arial, sans-serif; font-weight: 800;
    font-size: 27px; color: var(--black); margin-bottom: 14px;
  }
  .content p { font-size: 14.4px; line-height: 1.42; margin-bottom: 16px; }
  .features { position: absolute; top: 762px; left: 34px; right: 34px; }
  .features h2 {
    font-family: "Montserrat", Arial, sans-serif; font-weight: 800;
    font-size: 27px; color: var(--black); margin-bottom: 22px;
  }
  .feature-list { display: flex; gap: 60px; }
  .feature { width: 172px; text-align: center; }
  .feature .icon {
    width: 172px; height: 128px; background: var(--red);
    display: flex; align-items: center; justify-content: center;
  }
  .feature .label {
    font-family: "Montserrat", Arial, sans-serif; font-weight: 800;
    font-size: 19px; margin-top: 12px; color: var(--black);
  }
  .footer { position: absolute; left: 0; bottom: 0; width: 849px; height: 188px; }
  .footer .brand {
    position: absolute; left: 34px; top: 52px; display: flex; align-items: center; gap: 14px;
  }
  .brand .mark { width: 26px; height: 26px; background: var(--red); }
  .brand .name {
    font-family: "Montserrat", Arial, sans-serif; font-weight: 900;
    font-size: 56px; color: var(--black); letter-spacing: 2px;
  }
  .footer .contact {
    position: absolute; right: 0; top: 0; width: 540px; height: 188px;
    background: var(--black); color: var(--white); padding: 30px 30px 0 36px;
  }
  .contact .heading { font-family: "Montserrat", Arial, sans-serif; font-weight: 800; font-size: 17px; }
  .contact .cities { font-size: 14px; margin-top: 4px; }
  .contact .web {
    font-family: "Montserrat", Arial, sans-serif; font-weight: 800;
    font-size: 26px; margin-top: 30px;
  }
  .footer .accent { position: absolute; left: 0; bottom: 0; width: 309px; height: 14px; background: var(--red); }
</style>
</head>
<body>
<div class="flyer">
  <section class="hero">
    <h1>SEE THE PRISM DIFFERENCE IN ACTION</h1>
    <p>PRISM LED video walls bring vibrant, engaging displays to your school. Perfect for assemblies, student engagement, fundraising, sports scoreboards and special events. Our Team can have a PRISM LED video wall designed, installed and fully operational in time for the 2026 school year.</p>
    <p>Experience the impact first-hand with a free on-site demonstration at your school. Our team will show you how easy it is to transform your learning spaces with PRISM LED video walls.</p>
  </section>

  <div class="gallery">
    <div class="shot shot-hall" role="img" aria-label="LED video wall in a school assembly hall"></div>
    <div class="shot shot-outdoor" role="img" aria-label="Outdoor LED video wall on a school building"></div>
    <div class="shot shot-sports" role="img" aria-label="LED video wall used as a sports scoreboard"></div>
  </div>

  <section class="content">
    <h2>DIGITAL SIGNAGE FOR EDUCATIONAL VENUES</h2>
    <p>Eye-grabbing displays are the key to providing students with an immersive and all-around experience at all education levels. Whether it is to display the score of a game, share educational messages you cannot go wrong with PRISM LED Video Wall.</p>
    <p>Capture your student’s attention with ultra-high-resolution screens in any size, shape and curve. Improve your bottom line by promoting future events, running attractive advertisements for your partners or pitching great deals at your concession stands.</p>
  </section>

  <section class="features">
    <h2>FEATURES</h2>
    <div class="feature-list">
      <div class="feature">
        <div class="icon">
          <svg width="70" height="70" viewBox="0 0 70 70" fill="none" stroke="#fff" stroke-width="3" stroke-linecap="round" stroke-linejoin="round">
            <path d="M35 30 C28 22 18 26 22 34 L35 44 L48 34 C52 26 42 22 35 30 Z"/>
            <path d="M8 56 L20 50 L36 54 L52 48 C56 47 58 51 54 53 L38 60 L20 60 L8 64"/>
          </svg>
        </div>
        <div class="label">Support</div>
      </div>
      <div class="feature">
        <div class="icon">
          <svg width="70" height="70" viewBox="0 0 70 70" fill="none" stroke="#fff" stroke-width="3" stroke-linecap="round">
            <circle cx="35" cy="35" r="11"/>
            <path d="M35 8v9M35 53v9M8 35h9M53 35h9M16 16l6 6M48 48l6 6M16 54l6-6M48 22l6-6"/>
          </svg>
        </div>
        <div class="label">Brightness</div>
      </div>
      <div class="feature">
        <div class="icon">
          <svg width="72" height="72" viewBox="0 0 72 72" fill="none" stroke="#fff" stroke-width="3" stroke-linecap="round" stroke-linejoin="round">
            <path d="M32 6h8l2 8 6 3 7-4 6 6-4 7 3 6 8 2v8l-8 2-3 6 4 7-6 6-7-4-6 3-2 8h-8l-2-8-6-3-7 4-6-6 4-7-3-6-8-2v-8l8-2 3-6-4-7 6-6 7 4 6-3z"/>
            <circle cx="36" cy="36" r="13"/>
            <path d="M30 36l4 4 8-8"/>
          </svg>
        </div>
        <div class="label">Easy Installation</div>
      </div>
    </div>
  </section>

  <footer class="footer">
    <div class="brand">
      <span class="mark"></span>
      <span class="name">PRISM</span>
    </div>
    <div class="contact">
      <div class="heading">LOCATION:</div>
      <div class="cities">Northline AV Systems | Melbourne | Sydney | Perth | Brisbane</div>
      <div class="web">www.vantoraglow.com.au</div>
    </div>
    <div class="accent"></div>
  </footer>
</div>
</body>
</html>
```